Business card por a urban DJ, up scale audience target

Need a sober design, modern, conservative colors but i can consider some options, y play rnb, hip hop, EDM and top40.

Business card for contact and personal info, double sided, use logo attrached please; im 42 so i need a card acording to my age an target audience.

Target Market(s)

Adult people, up scale audience

Industry/Entity Type

Music Download

Contact Information for Business Card

Cel (318) 4207265518 www.lumadrift.com

Requirements
Must have
• open mind
Nice to have
• open mind
Should not have
• DJ

```html
<!DOCTYPE html>
<html lang="en">
<head>
<meta charset="utf-8">
<title>Lumadrift — Business Card</title>
<link rel="stylesheet" href="https://fonts.googleapis.com/css2?family=Open+Sans:wght@400;600;700;800&display=swap">
<style>
  :root {
    --ink: #0d0d0d;
    --paper: #ffffff;
    --stage: #2e2e2e;
    --muted: #444444;
  }
  * { box-sizing: border-box; margin: 0; padding: 0; }
  html, body { width: 1200px; height: 900px; overflow: hidden; }
  body {
    background: var(--stage);
    font-family: "Open Sans", Arial, sans-serif;
    display: flex;
    flex-direction: column;
    align-items: center;
    justify-content: center;
    gap: 48px;
  }
  .card {
    position: relative;
    width: 640px;
    height: 366px;
    box-shadow: 0 12px 28px rgba(0,0,0,.45);
  }
  .card-front {
    background: var(--ink);
    color: var(--paper);
    display: flex;
    flex-direction: column;
    align-items: center;
    justify-content: center;
  }
  .brand-name {
    font-weight: 800;
    font-size: 110px;
    line-height: 1;
    letter-spacing: 4px;
  }
  .card-front .site {
    margin-top: 14px;
    font-size: 22px;
    letter-spacing: 6px;
  }
  .card-back {
    background: var(--paper);
    color: var(--ink);
  }
  .card-back .brand-name {
    position: absolute;
    top: 38px;
    left: 0;
    width: 100%;
    text-align: center;
    font-size: 90px;
    color: var(--ink);
  }
  .level-meter {
    position: absolute;
    left: 0;
    top: 170px;
    width: 640px;
    height: 90px;
  }
  .contact-row {
    position: absolute;
    right: 40px;
    bottom: 40px;
    display: flex;
    align-items: center;
    gap: 14px;
  }
  .person { text-align: right; }
  .person-name { font-weight: 700; font-size: 19px; }
  .person-role { font-size: 11px; color: var(--muted); letter-spacing: 1px; }
  .divider { width: 1px; height: 40px; background: var(--ink); }
  .contact-list { list-style: none; font-size: 13px; color: var(--muted); }
  .contact-list li { display: flex; align-items: center; gap: 6px; line-height: 1.6; }
  .contact-list svg { width: 11px; height: 11px; }
</style>
</head>
<body>
  <section class="card card-front">
    <div class="brand-name">LUMA</div>
    <div class="site">www.lumadrift.com</div>
  </section>

  <section class="card card-back">
    <div class="brand-name">LUMA</div>
    <svg class="level-meter" viewBox="0 0 640 90" fill="#0d0d0d" aria-hidden="true">
      <rect x="0" y="84" width="640" height="6"/>
      <rect x="2" y="60" width="12" height="30"/><rect x="18" y="50" width="12" height="40"/>
      <rect x="34" y="66" width="12" height="24"/><rect x="50" y="44" width="12" height="46"/>
      <rect x="66" y="56" width="12" height="34"/><rect x="82" y="72" width="12" height="18"/>
      <rect x="98" y="48" width="12" height="42"/><rect x="114" y="62" width="12" height="28"/>
      <rect x="130" y="76" width="12" height="14"/><rect x="146" y="54" width="12" height="36"/>
      <rect x="162" y="40" width="12" height="50"/><rect x="178" y="68" width="12" height="22"/>
      <rect x="194" y="58" width="12" height="32"/><rect x="210" y="78" width="12" height="12"/>
      <rect x="226" y="46" width="12" height="44"/><rect x="242" y="64" width="12" height="26"/>
      <rect x="258" y="52" width="12" height="38"/><rect x="274" y="74" width="12" height="16"/>
      <rect x="290" y="42" width="12" height="48"/><rect x="306" y="60" width="12" height="30"/>
      <rect x="322" y="70" width="12" height="20"/><rect x="338" y="50" width="12" height="40"/>
      <rect x="354" y="36" width="12" height="54"/><rect x="370" y="62" width="12" height="28"/>
      <rect x="386" y="78" width="12" height="12"/><rect x="402" y="56" width="12" height="34"/>
      <rect x="418" y="44" width="12" height="46"/><rect x="434" y="66" width="12" height="24"/>
      <rect x="450" y="30" width="12" height="60"/><rect x="466" y="54" width="12" height="36"/>
      <rect x="482" y="72" width="12" height="18"/><rect x="498" y="40" width="12" height="50"/>
      <rect x="514" y="24" width="12" height="66"/><rect x="530" y="58" width="12" height="32"/>
      <rect x="546" y="34" width="12" height="56"/><rect x="562" y="68" width="12" height="22"/>
      <rect x="578" y="20" width="12" height="70"/><rect x="594" y="46" width="12" height="44"/>
      <rect x="610" y="28" width="12" height="62"/><rect x="626" y="14" width="12" height="76"/>
    </svg>
    <div class="contact-row">
      <div class="person">
        <div class="person-name">Marco Vale</div>
        <div class="person-role">CEO</div>
      </div>
      <div class="divider"></div>
      <ul class="contact-list">
        <li>
          <svg viewBox="0 0 12 12" aria-hidden="true"><rect x="3" y="0.5" width="6" height="11" rx="1" fill="none" stroke="#444" stroke-width="1.2"/><circle cx="6" cy="9.5" r=".8" fill="#444"/></svg>
          (318) 4207265518
        </li>
        <li>
          <svg viewBox="0 0 12 12" aria-hidden="true"><circle cx="6" cy="6" r="5" fill="none" stroke="#444" stroke-width="1.2"/><ellipse cx="6" cy="6" rx="2.2" ry="5" fill="none" stroke="#444" stroke-width="1"/><line x1="1" y1="6" x2="11" y2="6" stroke="#444" stroke-width="1"/></svg>
          www.lumadrift.com
        </li>
      </ul>
    </div>
  </section>
</body>
</html>
```